Progressive Flow Chart

Looking for a progressive flow chart centered and branching off. They all build on each other 1-3. There will be 3 different pages.

Target Market(s)

Business Owners - High Net worth Individuals

Industry/Entity Type

Finance & Business Consulting

Font styles to use
Serif

Colors
0054AA
0677BA
7BADD7
CADEEF
E8F1F8
0094D4
00A9DD
6FCCEA
C7EBF8
E9F6FB
00AB8E
00BBA5
67D7C9
C6EFE9
E9F9F6

Requirements
Nice to have
• Clean, simple, and approachable.
Should not have
• Very Busy

```html
<!DOCTYPE html>
<html lang="en">
<head>
<meta charset="utf-8">
<title>Living Trust Structure</title>
<link href="https://fonts.googleapis.com/css2?family=Poppins:wght@600;700;800&display=swap" rel="stylesheet">
<style>
  :root {
    --page: #ffffff;
    --sheet: #f1f1f1;
    --navy: #0d1436;
    --sky: #29aee0;
    --teal: #12e0c4;
    --white: #ffffff;
    --ink: #1a1a1a;
  }
  html, body { margin: 0; padding: 0; width: 1200px; height: 1200px; overflow: hidden; background: var(--page); }
  .chart { display: block; width: 1200px; height: 848px; margin-top: 176px; font-family: 'Poppins', sans-serif; }
  .sheet { fill: var(--sheet); }
  .footer-band { fill: var(--navy); }
  .box-navy { fill: var(--navy); }
  .box-grad { fill: url(#boxGradient); }
  .badge-navy { fill: var(--navy); }
  .badge-teal { fill: var(--teal); }
  .stitch { fill: none; stroke: var(--white); stroke-width: 3; stroke-dasharray: 14 8; }
  .link-dash { stroke: var(--ink); stroke-width: 3; stroke-dasharray: 12 8; }
  .flow { fill: none; stroke: var(--ink); stroke-width: 2.5; }
  .badge-num { font-weight: 800; font-size: 44px; fill: var(--white); text-anchor: middle; }
  .title-white { font-weight: 800; font-size: 42px; fill: var(--white); text-anchor: middle; }
  .title-sky { font-weight: 800; font-size: 42px; fill: var(--sky); text-anchor: middle; }
  .note { font-weight: 700; font-size: 15px; fill: var(--white); text-anchor: middle; }
  .flow-label { font-weight: 700; font-size: 16px; fill: var(--ink); }
  .trust-ring { fill: url(#ringGradient); }
  .trust-core { fill: var(--navy); stroke: var(--white); stroke-width: 5; }
  .arc-label { font-weight: 700; font-size: 36px; fill: var(--white); letter-spacing: 2px; }
  .firm-name { font-weight: 700; font-size: 22px; fill: var(--sky); text-anchor: middle; }
</style>
</head>
<body>
<svg class="chart" viewBox="107 358 1718 1214" xmlns="http://www.w3.org/2000/svg" aria-label="Living trust flow chart">
  <defs>
    <linearGradient id="boxGradient" x1="0" y1="0" x2="0" y2="1">
      <stop offset="0" stop-color="#29aee0"/>
      <stop offset="1" stop-color="#12e0c4"/>
    </linearGradient>
    <linearGradient id="ringGradient" x1="0" y1="0" x2="0" y2="1">
      <stop offset="0" stop-color="#29aee0"/>
      <stop offset="1" stop-color="#12e0c4"/>
    </linearGradient>
    <marker id="arrowHead" viewBox="0 0 12 12" refX="11" refY="6" markerWidth="12" markerHeight="12" markerUnits="userSpaceOnUse" orient="auto-start-reverse">
      <path d="M1 1 L11 6 L1 11" fill="none" stroke="#1a1a1a" stroke-width="2"/>
    </marker>
    <marker id="midHead" viewBox="0 0 12 12" refX="6" refY="6" markerWidth="14" markerHeight="14" markerUnits="userSpaceOnUse" orient="auto">
      <path d="M1 1 L8 6 L1 11" fill="none" stroke="#1a1a1a" stroke-width="2"/>
    </marker>
    <clipPath id="clipCrt"><path d="M283 450 H640 Q665 450 665 475 V628 L600 698 H283 Q258 698 258 673 V475 Q258 450 283 450 Z"/></clipPath>
    <clipPath id="clipDaf"><rect x="765" y="452" width="405" height="246" rx="26"/></clipPath>
    <clipPath id="clipGrats"><path d="M1292 450 H1650 Q1675 450 1675 475 V673 Q1675 698 1650 698 H1335 L1267 628 V475 Q1267 450 1292 450 Z"/></clipPath>
    <clipPath id="clipBank"><path d="M278 850 H525 Q500 973 527 1096 H278 Q258 1096 258 1076 V870 Q258 850 278 850 Z"/></clipPath>
    <clipPath id="clipEstate"><path d="M283 1240 H600 L665 1310 V1463 Q665 1488 640 1488 H283 Q258 1488 258 1463 V1265 Q258 1240 283 1240 Z"/></clipPath>
    <clipPath id="clipBusiness"><rect x="765" y="1240" width="405" height="248" rx="26"/></clipPath>
    <clipPath id="clipInsurance"><path d="M1335 1240 H1650 Q1675 1240 1675 1265 V1463 Q1675 1488 1650 1488 H1292 Q1267 1488 1267 1463 V1310 Z"/></clipPath>
  </defs>

  <rect class="sheet" x="107" y="358" width="1718" height="1214"/>
  <rect class="footer-band" x="107" y="1537" width="1718" height="35"/>

  <!-- connectors between tier three -->
  <line class="link-dash" x1="667" y1="557" x2="757" y2="557"/>
  <line class="link-dash" x1="1172" y1="557" x2="1262" y2="557"/>

  <!-- tier three: CRT -->
  <g class="node node-crt" clip-path="url(#clipCrt)">
    <rect class="box-grad" x="258" y="450" width="407" height="248"/>
    <path class="stitch" d="M282 460 H640 Q652 460 652 472 V622 L592 688 H282 Q272 688 272 678 V470 Q272 460 282 460 Z"/>
    <circle class="badge-navy" cx="298" cy="482" r="50"/>
  </g>
  <text class="badge-num" x="296" y="503">3</text>
  <text class="title-white" x="461" y="598">CRT</text>

  <!-- tier three: DAF -->
  <g class="node node-daf" clip-path="url(#clipDaf)">
    <rect class="box-navy" x="765" y="452" width="405" height="246"/>
    <rect class="stitch" x="777" y="462" width="381" height="226" rx="20"/>
    <circle class="badge-teal" cx="965" cy="472" r="56"/>
  </g>
  <text class="badge-num" x="965" y="503">3</text>
  <text class="title-sky" x="965" y="597">DAF</text>

  <!-- tier three: GRATs / IDGTs -->
  <g class="node node-grats" clip-path="url(#clipGrats)">
    <rect class="box-grad" x="1267" y="450" width="408" height="248"/>
    <path class="stitch" d="M1290 460 H1652 Q1662 460 1662 470 V678 Q1662 688 1652 688 H1340 L1279 622 V470 Q1279 460 1290 460 Z"/>
    <circle class="badge-navy" cx="1635" cy="482" r="50"/>
  </g>
  <text class="badge-num" x="1637" y="503">3</text>
  <text class="title-white" x="1471" y="601">GRATS' IDGT'S</text>

  <!-- flows -->
  <line class="flow" x1="743" y1="970" x2="512" y2="970" marker-end="url(#arrowHead)"/>
  <text class="flow-label" x="594" y="960">INVEST</text>

  <path class="flow" d="M437 1240 Q400 1170 388 1098" marker-end="url(#arrowHead)"/>
  <text class="flow-label" transform="translate(400 1214) rotate(-78)">INTEREST</text>

  <path class="flow" d="M485 1100 Q500 1180 545 1238" marker-end="url(#arrowHead)"/>
  <text class="flow-label" transform="translate(510 1218) rotate(-82)">INVESTMENT</text>

  <line class="flow" x1="550" y1="1240" x2="782" y2="1093" marker-end="url(#arrowHead)"/>
  <path class="flow" d="M550 1240 L666 1166" marker-end="url(#midHead)"/>
  <text class="flow-label" transform="translate(575 1214) rotate(-32)">INCOME</text>

  <line class="flow" x1="485" y1="1098" x2="965" y2="1240"/>
  <path class="flow" d="M485 1098 L740 1173" marker-end="url(#midHead)"/>

  <line class="flow" x1="965" y1="1238" x2="965" y2="1195" marker-start="url(#arrowHead)" marker-end="url(#arrowHead)"/>
  <text class="flow-label" x="988" y="1224">INCOME</text>

  <path class="flow" d="M765 1430 Q710 1405 665 1368" marker-end="url(#arrowHead)"/>
  <text class="flow-label" transform="translate(696 1374) rotate(30)">RENT</text>

  <line class="flow" x1="1183" y1="1028" x2="1502" y2="1237"/>
  <path class="flow" d="M1183 1028 L1362 1145" marker-end="url(#midHead)"/>
  <line class="flow" x1="1443" y1="1240" x2="1168" y2="1066"/>
  <path class="flow" d="M1443 1240 L1278 1136" marker-end="url(#midHead)"/>

  <!-- centre: living trust -->
  <circle class="trust-ring" cx="966" cy="970" r="222"/>
  <circle class="trust-core" cx="966" cy="970" r="163"/>
  <path id="trustArc" d="M806 970 A160 160 0 0 1 1126 970" transform="rotate(5 966 970)" fill="none" transform-origin="966 970"/>
  <path id="trustArcOuter" d="M781 970 A185 185 0 0 1 1151 970" fill="none"/>
  <text class="arc-label"><textPath href="#trustArcOuter" startOffset="50%" text-anchor="middle">1. LIVING TRUST</textPath></text>
  <text class="title-white" x="962" y="961">YOU</text>
  <text class="title-white" x="966" y="1012">TRUSTEE</text>

  <!-- tier two: bank -->
  <g class="node node-bank" clip-path="url(#clipBank)">
    <rect class="box-navy" x="258" y="850" width="270" height="246"/>
    <path class="stitch" d="M280 861 H511 Q490 973 512 1084 H280 Q271 1084 271 1075 V870"/>
    <circle class="badge-teal" cx="302" cy="880" r="46"/>
  </g>
  <text class="badge-num" x="299" y="905">2</text>
  <text class="title-sky" style="font-size:32px" x="382" y="952">BANK</text>
  <text class="note" x="382" y="981">MAKES</text>
  <text class="note" x="382" y="1001">INVESTMENTS TO REAL</text>
  <text class="note" x="382" y="1020">ESTATE + BUSINESS</text>

  <!-- advisory firm card -->
  <g class="node node-firm">
    <path class="box-navy" d="M1407 850 H1655 Q1675 850 1675 870 V1076 Q1675 1096 1655 1096 H1407 Q1432 973 1407 850 Z"/>
    <path class="stitch" d="M1423 861 H1652 Q1662 861 1662 871 V1074 Q1662 1084 1652 1084 H1422 Q1444 973 1423 861 Z"/>
  </g>
  <text class="firm-name" x="1548" y="966">ORVANE</text>
  <text class="firm-name" x="1548" y="996" style="font-size:15px">WEALTH PARTNERS</text>

  <!-- tier one: real estate -->
  <g class="node node-estate" clip-path="url(#clipEstate)">
    <rect class="box-grad" x="258" y="1240" width="407" height="248"/>
    <path class="stitch" d="M282 1250 H592 L652 1316 V1466 Q652 1476 642 1476 H282 Q272 1476 272 1466 V1260 Q272 1250 282 1250 Z"/>
    <circle class="badge-navy" cx="298" cy="1276" r="50"/>
  </g>
  <text class="badge-num" x="296" y="1297">1</text>
  <text class="title-white" x="461" y="1380">REAL ESTATE</text>
  <text class="title-white" style="font-size:34px" x="461" y="1425">LLC</text>

  <!-- tier one: business -->
  <g class="node node-business" clip-path="url(#clipBusiness)">
    <rect class="box-navy" x="765" y="1240" width="405" height="248"/>
    <rect class="stitch" x="778" y="1250" width="379" height="226" rx="20"/>
    <circle class="badge-teal" cx="965" cy="1260" r="56"/>
  </g>
  <text class="badge-num" x="965" y="1297">1</text>
  <text class="title-sky" x="965" y="1380">BUSINESS</text>
  <text class="note" x="965" y="1420">LLC-MEMBER/MANAGER</text>
  <text class="note" x="965" y="1440">CORP= PRESIDENT</text>

  <!-- tier two: insurance -->
  <g class="node node-insurance" clip-path="url(#clipInsurance)">
    <rect class="box-grad" x="1267" y="1240" width="408" height="248"/>
    <path class="stitch" d="M1340 1250 H1652 Q1662 1250 1662 1260 V1466 Q1662 1476 1652 1476 H1292 Q1282 1476 1282 1466 V1312 Z"/>
    <circle class="badge-navy" cx="1635" cy="1276" r="50"/>
  </g>
  <text class="badge-num" x="1637" y="1297">2</text>
  <text class="title-white" x="1471" y="1380">INSURANCE</text>
</svg>
</body>
</html>
```